Interior design service, along with home organization, packing, and staging, home and business. As well as staging in conjunction with real estate sales.
Updates

Love many of your designs and will be choosing today. To inform you of the exact details needed, the name of the company is "Flourish by Marnie T" , my phone number and e-,ail need to be included. i also need either description or some sort of bullet points that give an idea of the following:

- Interior design for home and business
- Home organization and packing
- Staging for personal and professional space
- Real estate stagingĀ 

Thank you

Target Market(s)

wide audience, but most importantly people looking for a quality service

Industry/Entity Type

Real Estate

Contact Information for Business Card

Flourish By Marnie T
Marnie Tolvery
(555)687-3914
mtbrisco@postwell.example

Requirements
Must have
• I'm 29 so i want my card to reflect something professional but still fresh. I don't have any specific photos or quotes that Ive included, however I like the card to reflect a personal touch, which is what I'm seeking from this service in the design of my card. Thanks!

```html
<!DOCTYPE html>
<html lang="en">
<head>
<meta charset="utf-8">
<title>Flourish By Marnie T — Business Card</title>
<link rel="stylesheet" href="https://fonts.googleapis.com/css2?family=Marcellus&family=Federo&display=swap">
<style>
  :root {
    --stage: #4a4a4a;
    --blue-deep: #3f74c0;
    --blue-mid: #4f8fcf;
    --blue-light: #6cbce0;
    --band: #3d7ccb;
    --white: #ffffff;
    --ink-blue: #2a78c8;
    --ink-bright: #2c9fdf;
    --rule-blue: #2c6fbf;
    --frame-cyan: #66cbe9;
    --tile-pale: #e4eefa;
  }
  * { margin: 0; padding: 0; box-sizing: border-box; }
  html, body { width: 1200px; height: 960px; overflow: hidden; }
  body { background: var(--stage); position: relative; }

  .card { position: absolute; overflow: hidden; }

  /* Front */
  .card-front { left: 188px; top: 40px; width: 600px; height: 352px; }
  .front-texture {
    position: absolute; inset: 0;
    background: linear-gradient(100deg, var(--blue-deep) 0%, var(--blue-mid) 50%, var(--blue-light) 100%);
  }
  .front-band { position: absolute; background: var(--band); opacity: .9; }
  .front-band--top { left: 0; top: 35px; width: 565px; height: 34px; }
  .front-band--bottom { left: 34px; top: 234px; right: 0; height: 32px; }
  .front-frame { position: absolute; inset: 10px; border: 1.5px solid rgba(255,255,255,.85); }
  .front-headline {
    position: absolute; left: 40px; top: 84px;
    font-family: "Marcellus", serif; font-weight: 400; color: var(--white); line-height: 1;
  }
  .front-headline .lead { display: block; font-size: 43px; }
  .front-headline .emphasis { display: block; font-size: 62px; margin: 8px 0 0 20px; }
  .service-list {
    position: absolute; left: 40px; top: 281px;
    display: grid; grid-template-columns: 310px 200px; column-gap: 20px; row-gap: 9px;
    list-style: none;
    font-family: "Marcellus", serif; font-size: 14px; line-height: 1; color: var(--white);
    white-space: nowrap;
  }
  .service-list li { display: flex; align-items: center; gap: 8px; }
  .service-list li::before {
    content: ""; width: 6px; height: 6px; background: var(--white); flex: none;
  }

  /* Back */
  .card-back { left: 457px; top: 432px; width: 598px; height: 350px; background: var(--white); }
  .back-texture {
    position: absolute; inset: 0;
    background:
      linear-gradient(180deg, rgba(228,238,250,.9) 0%, rgba(255,255,255,0) 28%, rgba(255,255,255,0) 70%, rgba(228,238,250,.9) 100%),
      linear-gradient(90deg, rgba(255,255,255,0) 40%, var(--tile-pale) 100%);
  }
  .back-frame { position: absolute; inset: 9px; border: 1.5px solid var(--frame-cyan); }
  .back-text { position: absolute; font-family: "Federo", sans-serif; line-height: 1; white-space: nowrap; }
  .company-prefix { left: 55px; top: 38px; font-size: 14px; color: var(--ink-blue); }
  .company-name { left: 91px; top: 62px; font-size: 36px; color: var(--ink-bright); }
  .contact-name-block { right: 321px; top: 184px; text-align: right; color: var(--ink-blue); }
  .contact-name-block .label { font-size: 24px; display: block; }
  .contact-name-block .value { font-size: 19px; display: block; margin-top: 10px; }
  .divider { position: absolute; left: 295px; top: 144px; width: 7px; height: 144px; background: var(--rule-blue); }
  .contact-details { left: 311px; top: 152px; color: var(--ink-blue); }
  .contact-details .label { display: block; font-size: 24px; }
  .contact-details .value { display: block; font-size: 21px; margin-top: 8px; }
  .contact-details .value--email { font-size: 17px; }
  .contact-details .group + .group { margin-top: 16px; }
</style>
</head>
<body>
  <section class="card card-front" aria-label="Card front">
    <div class="front-texture" role="img" aria-label="Blue mosaic tile pattern background"></div>
    <div class="front-band front-band--top"></div>
    <div class="front-band front-band--bottom"></div>
    <div class="front-frame"></div>
    <h1 class="front-headline">
      <span class="lead">Are you looking for a</span>
      <span class="emphasis">quality service??</span>
    </h1>
    <ul class="service-list">
      <li>Interior design for home &amp; business</li>
      <li>Home organization &amp; packing</li>
      <li>Staging for personal &amp; professional spaces</li>
      <li>Real estate staging</li>
    </ul>
  </section>

  <section class="card card-back" aria-label="Card back">
    <div class="back-texture" role="img" aria-label="Faint pale blue mosaic tile pattern"></div>
    <div class="back-frame"></div>
    <p class="back-text company-prefix">Flourish By,</p>
    <p class="back-text company-name">Marnie T</p>
    <div class="back-text contact-name-block">
      <span class="label">Name</span>
      <span class="value">Marnie Tolvery</span>
    </div>
    <div class="divider"></div>
    <div class="back-text contact-details">
      <div class="group">
        <span class="label">Phone</span>
        <span class="value">(555)687-3914</span>
      </div>
      <div class="group">
        <span class="label">Email</span>
        <span class="value value--email">mtbrisco@postwell.example</span>
      </div>
    </div>
  </section>
</body>
</html>
```